Layout for site fence advertising - length approx. 250 cm x 125 cm

The advertising will later be printed on a PVC film and used for events or on sports fields.

Main services :
Your regional contact at
Real estate and business financing
independent insurance advice

```html
<!DOCTYPE html>
<html lang="en">
<head>
<meta charset="utf-8">
<title>Site Fence Banner – Brenner Finanzberatung</title>
<link rel="stylesheet" href="https://fonts.googleapis.com/css2?family=Poppins:wght@500;600;800&family=Oswald:wght@600;700&display=swap">
<style>
  :root {
    --brand-blue: #1b57bd;
    --brand-red: #8a2222;
    --ink: #1f1f1f;
    --muted: #4a4a4a;
    --paper: #ffffff;
    --page: #ffffff;
    --photo-light: #e7cdbd;
    --photo-dark: #2b2a35;
  }
  * { margin: 0; padding: 0; box-sizing: border-box; }
  html, body {
    width: 929px; height: 1200px; overflow: hidden;
    background: var(--page);
  }
  .fence-banner {
    position: absolute; left: 20px; top: 378px;
    width: 889px; height: 444px;
    background: var(--paper);
    box-shadow: 0 2px 8px rgba(0,0,0,.35);
    overflow: hidden;
    font-family: "Poppins", sans-serif;
  }
  .banner-shapes { position: absolute; inset: 0; }
  .brand {
    position: absolute; left: 118px; top: 38px;
    display: flex; align-items: center; gap: 14px;
  }
  .brand-dot {
    width: 64px; height: 64px; border-radius: 50%;
    border: 5px solid var(--brand-blue);
  }
  .brand-rule { width: 2px; height: 106px; background: #555; }
  .brand-text { display: flex; flex-direction: column; gap: 2px; }
  .brand-name {
    font-weight: 600; font-size: 21px; color: var(--brand-blue); line-height: 1.1;
  }
  .brand-tagline {
    font-weight: 500; font-size: 15px; color: var(--muted); line-height: 1.2;
  }
  .headline {
    position: absolute; left: 0; top: 150px; width: 612px;
    text-align: center; color: var(--paper);
    font-weight: 800; font-size: 45px; line-height: 48px;
    letter-spacing: -0.5px;
  }
  .regional {
    position: absolute; left: 0; top: 264px; width: 640px;
    text-align: center; color: var(--ink);
    font-weight: 800; font-size: 34px; line-height: 50px;
  }
  .contact-row {
    position: absolute; left: 56px; top: 316px; height: 49px;
    display: flex; align-items: center; gap: 22px;
    font-family: "Oswald", sans-serif; font-weight: 700;
    font-size: 29px; color: var(--paper);
  }
  .contact-item { display: flex; align-items: center; gap: 6px; }
  .contact-item svg { width: 24px; height: 24px; }
  .role-title {
    position: absolute; left: 48px; top: 365px; height: 79px;
    display: flex; align-items: center;
    font-family: "Oswald", sans-serif; font-weight: 700;
    font-size: 34px; color: var(--ink);
  }
  .advisor-name {
    position: absolute; left: 600px; top: 365px; width: 289px; height: 79px;
    display: flex; align-items: center; justify-content: center;
    font-family: "Oswald", sans-serif; font-weight: 600;
    font-size: 36px; color: var(--paper);
  }
</style>
</head>
<body>
  <section class="fence-banner">
    <svg class="banner-shapes" width="889" height="444" viewBox="0 0 889 444">
      <defs>
        <linearGradient id="portraitTone" x1="0" y1="0" x2="0" y2="1">
          <stop offset="0" stop-color="#f4f1ee"/>
          <stop offset="0.55" stop-color="var(--photo-light)"/>
          <stop offset="0.8" stop-color="var(--photo-dark)"/>
        </linearGradient>
      </defs>
      <g role="img" aria-label="Portrait photo of the advisor in a dark suit and white shirt">
        <path d="M690 255 A150 150 0 0 1 889 -40 L889 365 L680 365 Z" fill="url(#portraitTone)"/>
      </g>
      <circle class="accent-arc" cx="800" cy="95" r="160" fill="none" stroke="var(--brand-blue)" stroke-width="14"
              stroke-dasharray="0 502 370 200"/>
      <polygon class="band-blue" points="0,144 614,144 690,262 0,262" fill="var(--brand-blue)"/>
      <polygon class="band-red" points="0,316 693,316 680,365 0,365" fill="var(--brand-red)"/>
      <polygon class="name-tab" points="605,365 889,365 889,444 605,444 580,404" fill="var(--brand-blue)"/>
    </svg>

    <div class="brand">
      <div class="brand-dot"></div>
      <div class="brand-rule"></div>
      <div class="brand-text">
        <span class="brand-name">Brenner Finanzberatung GmbH</span>
        <span class="brand-tagline">Finanzieren, Versichern, Vorsorgen</span>
      </div>
    </div>

    <h1 class="headline">REAL ESTATE AND<br>BUSINESS FINANCING</h1>
    <p class="regional">YOUR REGIONAL CONTACT AT</p>

    <div class="contact-row">
      <span class="contact-item">
        <svg viewBox="0 0 24 24"><circle cx="12" cy="12" r="11" fill="#fff"/><path d="M8 6.5l2 2.4-1.1 1.6c.8 1.7 2 2.9 3.7 3.7l1.6-1.1 2.4 2-1 2c-4.3-.4-8-4.1-8.4-8.4z" fill="var(--brand-red)"/></svg>
        +43 660 214 5809
      </span>
      <span class="contact-item">
        <svg viewBox="0 0 24 24"><circle cx="12" cy="12" r="11" fill="#fff"/><circle cx="12" cy="12" r="6.5" fill="none" stroke="var(--brand-red)" stroke-width="1.6"/><path d="M5.5 12h13M12 5.5c-2.5 3.5-2.5 9.5 0 13M12 5.5c2.5 3.5 2.5 9.5 0 13" fill="none" stroke="var(--brand-red)" stroke-width="1.4"/></svg>
        www.der-brenner.at
      </span>
    </div>

    <p class="role-title">INDEPENDENT INSURANCE ADVISOR</p>
    <p class="advisor-name">MARKUS BRENNER</p>
  </section>
</body>
</html>
```